Business card design needed

A laid back coffee shop that has a great feel, that becomes a bar and grill at night. We are also wanting to cater for functions etc.
The business itself is painted dark blue/charcoal and has red doors.
Would like a logo that will be recognised when seen.

Industry/Entity Type

Coffee Shop

Contact Information for Business Card

The Lantern Coffee Bar & Grill
14b Wattle St
Merrindale NSW 2291
Ph. 02 4817 6230

Logo Text

Logo styles of interest
Emblem Logo
Abstract Logo
Wordmark Logo
Requirements
Must have
• A loyalty card on the back with 2 rows of 7 stamp spaces and a place to write a name and phone number (for a draw)

```html
<!DOCTYPE html>
<html lang="en">
<head>
<meta charset="utf-8">
<title>The Lantern Coffee Bar &amp; Grill – Loyalty Card</title>
<link href="https://fonts.googleapis.com/css2?family=Delius&display=swap" rel="stylesheet">
<style>
  :root {
    --page-bg: #ffffff;
    --ink: #111111;
    --stamp-ring: #111111;
    --stamp-fill: #ffffff;
    --brand-red: #e0231c;
    --stain-light: #fffaf0;
    --stain-mid: #fbe7bd;
    --stain-deep: #f6d28e;
    --card-edge: #e6e6e6;
  }
  * { box-sizing: border-box; margin: 0; padding: 0; }
  html, body {
    width: 1200px;
    height: 1000px;
    overflow: hidden;
    background: var(--page-bg);
  }
  body {
    position: relative;
    font-family: "Delius", "Comic Sans MS", sans-serif;
    color: var(--ink);
  }
  .loyalty-card {
    position: absolute;
    left: 45px;
    top: 160px;
    width: 1110px;
    height: 680px;
    border: 1px solid var(--card-edge);
    overflow: hidden;
  }
  .stain-area {
    position: absolute;
    inset: 0;
    background: linear-gradient(115deg, var(--stain-light) 0%, var(--stain-mid) 55%, var(--stain-deep) 100%);
  }
  .stamp-grid {
    position: absolute;
    left: 49px;
    top: 62px;
    display: grid;
    grid-template-columns: repeat(7, 116px);
    column-gap: 30px;
    row-gap: 24px;
  }
  .stamp {
    width: 116px;
    height: 116px;
    border-radius: 50%;
    border: 3px solid var(--stamp-ring);
    background: var(--stamp-fill);
  }
  .details {
    position: absolute;
    left: 50px;
    top: 376px;
  }
  .detail-row {
    display: flex;
    align-items: flex-end;
    height: 40px;
    margin-bottom: 43px;
  }
  .detail-label {
    width: 177px;
    font-size: 32px;
    line-height: 1;
  }
  .write-line {
    width: 653px;
    border-bottom: 2px dashed var(--ink);
    margin-bottom: 4px;
  }
  .business-name {
    position: absolute;
    left: 186px;
    top: 568px;
    font-size: 36px;
    letter-spacing: 2px;
    word-spacing: 14px;
    white-space: nowrap;
  }
  .brand-mark {
    position: absolute;
    right: 20px;
    top: 490px;
    width: 170px;
    text-align: center;
    font-size: 30px;
    line-height: 1;
    color: var(--brand-red);
    letter-spacing: 2px;
  }
</style>
</head>
<body>
  <main class="loyalty-card">
    <div class="stain-area" role="img" aria-label="Coffee cup ring stain across the card"></div>

    <section class="stamp-grid" aria-label="Loyalty stamps">
      <div class="stamp"></div><div class="stamp"></div><div class="stamp"></div><div class="stamp"></div><div class="stamp"></div><div class="stamp"></div><div class="stamp"></div>
      <div class="stamp"></div><div class="stamp"></div><div class="stamp"></div><div class="stamp"></div><div class="stamp"></div><div class="stamp"></div><div class="stamp"></div>
    </section>

    <section class="details">
      <div class="detail-row"><span class="detail-label">Name</span><span class="write-line"></span></div>
      <div class="detail-row"><span class="detail-label">Phone</span><span class="write-line"></span></div>
    </section>

    <p class="business-name">THE LANTERN Coffee Bar &amp; Grill</p>

    <div class="brand-mark">LANTERN</div>
  </main>
</body>
</html>
```